Podiatry clinic requires a modern revamp and editing of existing website.

I would like a fresh new look and updated information for my current business website. An easy to navigate site with prominent address and phone number for call to action. We are a podiatry clinic that focuses on general and sports podiatry.
I would like 4 pages; including Home page, About Us, Services & Contact.
www.brambleridgepodiatry.net

Target Market(s)

Active working professionals.

Industry/Entity Type

Medical

Coding

Coded - Design and coding required

Number of Pages Required

4 page

Font styles to use
Sans Serif

Colors
6b449b

Requirements
Must have
• A modern look with logo and active images; clean and uncluttered. Visible phone number and address for call to action.
• 4 pages - Home, About Us, Services, Contact.
• Home page - update address & service logos.
• About Us - update of personal information.
• Services - Revamp of existing page.
• Contact page to include Google map, email & phone number.
Nice to have
• Ability to add content easily; eg. a blog or adding video onto Home page.
• Link to Facebook page.

```html
<!DOCTYPE html>
<html lang="en">
<head>
<meta charset="utf-8">
<title>Bramble Ridge Podiatry</title>
<link href="https://fonts.googleapis.com/css2?family=Open+Sans:wght@400;600;700;800&family=Nunito+Sans:ital,wght@0,400;0,700;1,800&display=swap" rel="stylesheet">
<style>
:root{
  --purple:#6b449b;
  --purple-deep:#472c8a;
  --purple-btn:#7a5cc4;
  --orange:#f07a1e;
  --ink:#333333;
  --muted:#555555;
  --page:#e9e9ea;
  --footer:#1d1d1d;
  --white:#ffffff;
}
*{box-sizing:border-box;margin:0;padding:0}
html,body{width:1200px;height:2985px;overflow:hidden}
body{background:var(--page);font-family:"Open Sans",Arial,sans-serif;color:var(--ink);position:relative}
.site{position:absolute;left:16px;top:16px;width:1168px;height:2969px;background:var(--white)}
.abs{position:absolute}

/* header */
.brand{position:absolute;left:30px;top:30px;display:flex;align-items:center;gap:12px}
.brand-dot{width:26px;height:26px;border-radius:50%;background:var(--purple)}
.brand-name{font-weight:700;font-size:24px;color:var(--purple);width:150px;line-height:28px}
.header-contact{position:absolute;top:36px;display:flex;align-items:center;gap:12px;font-weight:700;font-size:17px;line-height:21px;color:#222}
.header-contact svg{flex:none}

/* nav */
.nav{position:absolute;left:0;top:160px;width:1168px;height:44px;background:var(--purple-deep);display:flex;padding-left:314px}
.nav a{display:block;height:44px;line-height:44px;padding:0 26px;color:var(--white);font-weight:700;font-size:14px;text-decoration:none;letter-spacing:.2px}
.nav a.is-active{background:var(--orange)}

/* hero */
.hero{position:absolute;left:0;top:204px;width:1168px;height:560px;background:linear-gradient(100deg,#5f6a7a 0%,#8a8f98 30%,#3c3f45 65%,#141518 100%)}
.hero-arrow{position:absolute;top:228px;width:48px;height:48px;background:var(--purple-deep);display:flex;align-items:center;justify-content:center}
.hero-copy{position:absolute;left:710px;top:170px;width:380px;color:var(--white)}
.hero-copy h1{font-size:25px;font-weight:700;margin-bottom:14px}
.hero-copy p{font-size:15px;line-height:21px}
.btn{display:inline-block;background:var(--purple-btn);color:var(--white);font-weight:700;font-size:14px;text-align:center;text-decoration:none;letter-spacing:.3px}
.hero-actions{position:absolute;left:710px;top:336px;display:flex;gap:12px}
.hero-actions .btn{width:180px;height:38px;line-height:38px}

/* treatment cards */
.treatment{position:absolute;top:728px;width:478px;height:436px;background:var(--white);box-shadow:0 2px 10px rgba(0,0,0,.12)}
.treatment::after{content:"";position:absolute;left:20px;right:20px;bottom:-22px;height:14px;background:radial-gradient(ellipse at center,rgba(0,0,0,.35),rgba(0,0,0,0) 70%)}
.treatment-photo{position:absolute;left:10px;top:10px;width:458px;height:230px;background:linear-gradient(135deg,#d9cfc9,#b7aba6 50%,#efe9e6)}
.treatment-badge{position:absolute;left:-24px;top:-20px;width:130px;height:130px;border-radius:50%;background:var(--orange);border:5px solid #fbd2b0;display:flex;align-items:center;justify-content:center;text-align:center;color:var(--white);font-weight:700;font-size:17px;line-height:20px}
.treatment-text{position:absolute;left:10px;top:262px;width:458px;font-size:13px;line-height:19px;color:var(--muted)}
.treatment .btn{position:absolute;left:149px;top:372px;width:180px;height:36px;line-height:36px}

/* about */
.about{position:absolute;left:0;top:1220px;width:1168px;height:558px;background:linear-gradient(120deg,#5a3f98,#4a2f88 55%,#3a2470)}
.section-title{position:absolute;left:0;width:100%;text-align:center;font-family:"Nunito Sans",sans-serif;font-size:28px}
.section-title em{font-weight:800}
.rule{position:absolute;height:1px}
.rule-mark{position:absolute;width:12px;height:12px;border-radius:50%}
.about-text{position:absolute;left:68px;top:188px;width:560px;color:var(--white);font-size:14px;line-height:20px}
.about-text p{margin-bottom:20px}
.about .btn-light{position:absolute;left:68px;top:436px;width:180px;height:36px;line-height:36px;background:var(--white);color:var(--purple-deep);font-weight:700;font-size:14px;text-align:center}
.video{position:absolute;left:668px;top:204px;width:440px;height:310px;background:var(--white);padding:6px;box-shadow:0 2px 8px rgba(0,0,0,.3)}
.video-frame{width:428px;height:256px;background:linear-gradient(180deg,#f3c97b,#e3a65e 45%,#6d6a66 80%,#3a3835)}
.video-bar{height:36px;display:flex;align-items:center;gap:12px;padding:0 8px;background:#e8e8e8}
.video-track{flex:1;height:8px;border-radius:4px;background:#9a9a9a;position:relative}
.video-track span{position:absolute;left:0;top:0;height:8px;width:34%;border-radius:4px;background:#c8161d}

/* blog */
.blog{position:absolute;left:0;top:1778px;width:1168px;height:632px;background:#f2f2f3}
.post{position:absolute;top:202px;width:336px;height:386px;background:var(--white)}
.post-photo{width:336px;height:210px}
.post h3{text-align:center;font-size:18px;font-weight:700;margin-top:20px;color:#222}
.post p{padding:0 24px;margin-top:8px;font-size:13px;line-height:18px;color:var(--muted);text-align:center}
.post .btn{position:absolute;left:84px;top:338px;width:168px;height:30px;line-height:30px;font-size:13px;border-radius:2px}

/* partners */
.partners{position:absolute;left:0;top:2410px;width:1168px;height:200px;background:var(--white)}
.partner{position:absolute;top:78px;height:46px;border-radius:6px}

/* footer */
.footer{position:absolute;left:0;top:2610px;width:1168px;height:324px;background:var(--footer);color:#cfcfcf}
.footer h4{position:absolute;top:50px;color:var(--white);font-size:15px;font-weight:700}
.footer .underline{position:absolute;top:78px;height:1px;background:#555}
.footer ul{list-style:none;position:absolute;top:106px;font-size:13px;line-height:22px}
.footer-contact{position:absolute;left:444px;top:106px;font-size:13px;line-height:20px}
.footer-contact .row{display:flex;gap:10px;margin-bottom:16px}
.map{position:absolute;left:732px;top:40px;width:402px;height:244px;background:linear-gradient(135deg,#eef0ea,#dde4e8 50%,#e8ecdf)}
.copyright{position:absolute;left:0;top:2934px;width:1168px;height:35px;background:var(--purple-deep);color:var(--white);font-size:10px;font-weight:700;line-height:35px;padding-left:32px;letter-spacing:.2px}
.social{position:absolute;right:20px;top:9px;display:flex;gap:6px}
.social span{width:17px;height:17px;border-radius:50%;background:var(--white)}
</style>
</head>
<body>
<div class="site">

  <header>
    <div class="brand"><span class="brand-dot"></span><span class="brand-name">Bramble Ridge Podiatry</span></div>
    <div class="header-contact" style="left:734px">
      <svg width="36" height="36" viewBox="0 0 36 36"><circle cx="18" cy="18" r="16" fill="none" stroke="#222" stroke-width="2.5"/><path d="M18 9a6 6 0 0 0-6 6c0 5 6 12 6 12s6-7 6-12a6 6 0 0 0-6-6z" fill="#222"/><circle cx="18" cy="15" r="2.2" fill="#fff"/></svg>
      <div>Level 4<br>27 Alder Lane<br>Fernvale 4021</div>
    </div>
    <div class="header-contact" style="left:970px;top:58px">
      <svg width="36" height="36" viewBox="0 0 36 36"><circle cx="18" cy="18" r="16" fill="none" stroke="#222" stroke-width="2.5"/><path d="M12 10c1-1 2.5-1 3 0l2 3c.5 1 0 2-1 2.5l-1 .6c.8 2 2.5 3.8 4.5 4.6l.6-1c.5-1 1.6-1.5 2.5-1l3 2c1 .5 1 2 0 3l-1.5 1.5c-5 1-13-7-12-12z" fill="#222"/></svg>
      <div>1300 482 905</div>
    </div>
  </header>

  <nav class="nav">
    <a class="is-active" href="#">HOME</a>
    <a href="#">ABOUT</a>
    <a href="#">OUR SERVICES</a>
    <a href="#">CONTACT US</a>
    <a href="#">BLOG</a>
  </nav>

  <section class="hero" role="img" aria-label="Runners' legs and shoes on a city road during a race">
    <div class="hero-arrow" style="left:0"><svg width="14" height="18" viewBox="0 0 14 18"><path d="M11 2 3 9l8 7" fill="none" stroke="#fff" stroke-width="3"/></svg></div>
    <div class="hero-arrow" style="right:0"><svg width="14" height="18" viewBox="0 0 14 18"><path d="M3 2l8 7-8 7" fill="none" stroke="#fff" stroke-width="3"/></svg></div>
    <div class="hero-copy">
      <h1>Welcome to Bramble Ridge Podiatry</h1>
      <p>We provide General Podiatry Treatment and some Specialised Services in relation to various foot conditions, including Sports Injuries, Orthotic Therapy and Nail Surgery.</p>
    </div>
    <div class="hero-actions"><a class="btn" href="#">VIEW SERVICES</a><a class="btn" href="#">REQUEST A CALL</a></div>
  </section>

  <article class="treatment" style="left:98px">
    <div class="treatment-photo" role="img" aria-label="Podiatrist treating a patient's foot"></div>
    <div class="treatment-badge">General<br>Treatments</div>
    <p class="treatment-text">At Bramble Ridge Podiatry, we provide general treatments including; Nails, Corns, Callus, Warts, Skin Disorders, Heel Pain, Heel Spurs, Arch Pain-Plantar Fasciitis, Ankle Pain, Shin Splints, Knee Paint, Bunions, Hammestoes and Toe Deformities</p>
    <a class="btn" href="#">LEARN MORE</a>
  </article>

  <article class="treatment" style="left:630px">
    <div class="treatment-photo" role="img" aria-label="Hands examining a bare foot"></div>
    <div class="treatment-badge">Specialised<br>Treatments</div>
    <p class="treatment-text">Our specialised treatments including; Diabetic Management, Nail Surgery, Biomechanical Assessment, Gait Analysis, and Orthotic Therapy.</p>
    <a class="btn" href="#">LEARN MORE</a>
  </article>

  <section class="about">
    <h2 class="section-title" style="top:58px;color:#fff;font-weight:400">About <em style="color:#b9a6ec">Bramble Ridge Podiatry</em></h2>
    <div class="rule" style="left:84px;width:1006px;top:120px;background:rgba(255,255,255,.45)"></div>
    <div class="rule-mark" style="left:578px;top:130px;background:#fff"></div>
    <div class="about-text">
      <p>Bramble Ridge Podiatry is a Podiatry clinic in the heart of Fernvale city centre. We are located between Alder &amp; Quill Streets in the Harbourline Business Centre.</p>
      <p>Our podiatrists are fully qualified health professionals who are able to diagnose, treat, manage or help to prevent all medical conditions that affect the feet and lower limb.</p>
      <p>We provide General Podiatry Treatment and some Specialised Services in relation to various foot conditions, including Sports Injuries, Orthotic Therapy and Nail Surgery. For Appointments or Enquiries please call us on <b>1300 482 905</b> or email: <b>info@brambleridgepodiatry.net</b></p>
    </div>
    <div class="btn-light">LEARN MORE</div>
    <div class="video">
      <div class="video-frame" role="img" aria-label="Video still of a runner at sunset on a waterfront path"></div>
      <div class="video-bar">
        <svg width="14" height="16" viewBox="0 0 14 16"><path d="M1 1l12 7-12 7z" fill="#777"/></svg>
        <div class="video-track"><span></span></div>
        <svg width="16" height="14" viewBox="0 0 16 14"><path d="M1 5h3l4-4v12l-4-4H1z" fill="#777"/></svg>
        <svg width="14" height="14" viewBox="0 0 14 14"><path d="M1 1l12 12M13 1 1 13" stroke="#444" stroke-width="2"/></svg>
      </div>
    </div>
  </section>

  <section class="blog">
    <h2 class="section-title" style="top:78px;color:#333;font-weight:400">Latest From <em style="color:var(--purple-deep)">the Blog</em></h2>
    <div class="rule" style="left:84px;width:1006px;top:140px;background:#ddd"></div>
    <div class="rule-mark" style="left:578px;top:132px;background:var(--purple-deep)"></div>

    <article class="post" style="left:46px">
      <div class="post-photo" role="img" aria-label="X-ray style image of feet with a highlighted heel" style="background:linear-gradient(135deg,#111,#3a3a3a 50%,#8a3a1a)"></div>
      <h3>Blog #1</h3>
      <p>Lorem ipsum dolor sit amet, consectetuer adipis cing elit, sed diam nonummy nibh euismod tinci dunt ut laoreet dolore magna aliquam.</p>
      <a class="btn" href="#">Read more</a>
    </article>
    <article class="post" style="left:418px">
      <div class="post-photo" role="img" aria-label="Running shoe on an outdoor track" style="background:linear-gradient(180deg,#7d6d50,#b59a70 55%,#d9c7a3)"></div>
      <h3>Blog #2</h3>
      <p>Lorem ipsum dolor sit amet, consectetuer adipis cing elit, sed diam nonummy nibh euismod tinci dunt ut laoreet dolore magna aliquam.</p>
      <a class="btn" href="#">Read more</a>
    </article>
    <article class="post" style="left:790px">
      <div class="post-photo" role="img" aria-label="Runner stretching by a city waterfront" style="background:linear-gradient(180deg,#d8e2ea,#b6c3cc 55%,#8b8e8f)"></div>
      <h3>Blog #3</h3>
      <p>Lorem ipsum dolor sit amet, consectetuer adipis cing elit, sed diam nonummy nibh euismod tinci dunt ut laoreet dolore magna aliquam.</p>
      <a class="btn" href="#">Read more</a>
    </article>
  </section>

  <section class="partners" aria-label="Health fund and association partners">
    <svg class="abs" style="left:46px;top:92px" width="16" height="20" viewBox="0 0 16 20"><path d="M12 2 4 10l8 8" fill="none" stroke="#555" stroke-width="2.5"/></svg>
    <svg class="abs" style="left:1120px;top:92px" width="16" height="20" viewBox="0 0 16 20"><path d="M4 2l8 8-8 8" fill="none" stroke="#555" stroke-width="2.5"/></svg>
    <div class="partner" style="left:114px;width:220px;background:#e2e2e2"></div>
    <div class="partner" style="left:384px;width:160px;background:#cfe6c7"></div>
    <div class="partner" style="left:594px;width:150px;background:#d8d2ee"></div>
    <div class="partner" style="left:794px;width:150px;background:#d3dff0"></div>
    <div class="partner" style="left:994px;width:60px;height:70px;top:66px;background:#d6d9ec"></div>
  </section>

  <footer class="footer">
    <div style="position:absolute;left:44px;top:124px;display:flex;align-items:center;gap:10px">
      <span class="brand-dot"></span><span class="brand-name" style="color:#a98ae0;font-size:22px">Bramble Ridge Podiatry</span>
    </div>
    <h4 style="left:276px">QUICK LINKS</h4>
    <div class="underline" style="left:276px;width:104px"></div>
    <ul style="left:276px">
      <li>Home</li><li>About Us</li><li>Services</li><li>Contact Us</li><li>Blog</li>
    </ul>
    <h4 style="left:444px">CONTACT</h4>
    <div class="underline" style="left:444px;width:240px"></div>
    <div class="footer-contact">
      <div class="row"><svg width="10" height="14" viewBox="0 0 10 14"><path d="M5 0a5 5 0 0 0-5 5c0 4 5 9 5 9s5-5 5-9a5 5 0 0 0-5-5z" fill="#7a5cc4"/></svg><div>Bramble Ridge Podiatry<br>Level 4<br>27 Alder Lane<br>Fernvale 4021</div></div>
      <div class="row" style="margin-top:24px"><svg width="12" height="12" viewBox="0 0 12 12"><path d="M2 1c1-1 2 0 2.5 1l1 1.5c.3.7-.2 1.3-.8 1.6.6 1.4 1.6 2.4 3 3 .3-.6.9-1.1 1.6-.8l1.5 1c1 .5 2 1.5 1 2.5-4 2-11-5-9.8-9.8z" fill="#7a5cc4"/></svg><div>1300 482 905</div></div>
      <div class="row" style="margin-top:24px"><svg width="12" height="10" viewBox="0 0 12 10"><rect x="0" y="0" width="12" height="10" rx="1" fill="#7a5cc4"/><path d="M0 1l6 4 6-4" fill="none" stroke="#1d1d1d" stroke-width="1"/></svg><div>info@brambleridgepodiatry.net</div></div>
    </div>
    <div class="map" role="img" aria-label="Street map showing the clinic location"></div>
  </footer>

  <div class="copyright">COPYRIGHT © 2016 BRAMBLE RIDGE PODIATRY. ALL RIGHTS RESERVED.
    <div class="social"><span></span><span></span></div>
  </div>
</div>
</body>
</html>
```